Easy Marinade Labels for Butchery Store

Need a set of labels designed for a Butchery Shop. They will sit in the top left corner of the packets as a triangle (7cm each side). Easy because the only major requirement is the label name and some small text saying "Please ask in store to see spec sheet for ingredients". Extra points for finding a fun way to incorporate the logo and/or images of food (garlic bulbs, chilli, spices ect) to enhance the label. List of Marinade Names below: GarlicPepper Mint & RosemarySatayBBQChilli Plum & GingerSundried Tomato & BasilBuffaloHoney SoyHoi-SinPer PeriSpicy CajunTeriyakiBlack Bean Ive also attached the logo and an example of how the label might sit on a packet of meat. Thanks

Target Market(s)

Butchery Deli Shop Customers

Industry/Entity Type

Food Store

Font styles to use
Serif
Sans Serif
Decorative
Other font styles liked:
• Fun font that isn't a generic Quellbrix Font?

Colors

Designer to choose colors to be used in the design.

Requirements
Must have
• Product Name
• Small text saying "Please ask in store to see spec sheet for ingredients"
Nice to have
• Photos of ingredients that would match that type of marinade - Chilli, Garlic, Spices.
• Fenly Oak Logo - not essential if it doesn't look good on the label / doesn't fit.

```html
<!DOCTYPE html>
<html lang="en">
<head>
<meta charset="utf-8">
<title>Sundried Tomato and Basil – Marinade Label</title>
<link rel="stylesheet" href="https://fonts.googleapis.com/css2?family=Caveat+Brush&family=Fira+Sans+Condensed:wght@700&display=swap">
<style>
  :root {
    --page-bg: #ffffff;
    --frame-yellow: #efe925;
    --tomato-red: #d8261d;
    --tomato-deep: #b81a14;
    --basil-green: #2f7b36;
    --basil-dark: #1f5a2a;
    --label-text: #ffffff;
  }
  html, body {
    margin: 0;
    padding: 0;
    width: 1200px;
    height: 900px;
    overflow: hidden;
    background: var(--page-bg);
  }
  .label-canvas {
    display: block;
    width: 1200px;
    height: 900px;
  }
  .label-frame {
    fill: none;
    stroke: var(--frame-yellow);
    stroke-width: 7;
    stroke-linejoin: miter;
  }
  .product-name {
    font-family: "Caveat Brush", "Comic Sans MS", cursive;
    fill: var(--label-text);
    text-transform: uppercase;
  }
  .name-swash {
    fill: none;
    stroke: var(--label-text);
    stroke-width: 7;
    stroke-linecap: round;
  }
  .spec-note {
    font-family: "Fira Sans Condensed", "Arial Narrow", sans-serif;
    font-weight: 700;
    font-size: 22px;
    letter-spacing: 2px;
    fill: var(--label-text);
  }
</style>
</head>
<body>
<svg class="label-canvas" viewBox="0 0 1200 900" xmlns="http://www.w3.org/2000/svg">
  <defs>
    <linearGradient id="ingredient-tones" x1="0" y1="0" x2="1" y2="1">
      <stop offset="0" stop-color="var(--basil-green)"/>
      <stop offset="0.25" stop-color="var(--tomato-red)"/>
      <stop offset="0.45" stop-color="var(--basil-dark)"/>
      <stop offset="0.65" stop-color="var(--tomato-deep)"/>
      <stop offset="1" stop-color="var(--basil-green)"/>
    </linearGradient>
  </defs>

  <polygon class="label-artwork" points="322,152 979,152 322,810"
           fill="url(#ingredient-tones)"
           role="img" aria-label="Painted illustration of sundried tomatoes and basil leaves"/>

  <polygon class="label-frame" points="318.5,148.5 987,148.5 318.5,818"/>

  <g class="product-name-block">
    <text class="product-name" x="349" y="259" font-size="80" textLength="251" lengthAdjust="spacingAndGlyphs">Sundried</text>
    <text class="product-name" x="357" y="343" font-size="100" textLength="235" lengthAdjust="spacingAndGlyphs">Tomato</text>
    <path class="name-swash" d="M420 384 C 450 378, 470 362, 508 370"/>
    <text class="product-name" x="431" y="428" font-size="58" textLength="72" lengthAdjust="spacingAndGlyphs">And</text>
    <path class="name-swash" d="M418 440 C 440 452, 470 428, 508 424"/>
    <text class="product-name" x="371" y="543" font-size="100" textLength="180" lengthAdjust="spacingAndGlyphs">Basil</text>
  </g>

  <g class="spec-note-block">
    <text class="spec-note" x="618" y="224" textLength="250" lengthAdjust="spacing">PLEASE ASK IN STORE</text>
    <text class="spec-note" x="618" y="254" textLength="219" lengthAdjust="spacing">TO SEE SPEC SHEET</text>
    <text class="spec-note" x="618" y="284" textLength="209" lengthAdjust="spacing">FOR INGREDIENTS</text>
  </g>
</svg>
</body>
</html>
```